Verodex business card

Business card for sustainable investment company called "Verodex". Verodex is an exchange platform selling carbon credits between buyers and sellers. Carbon Credits are an environmental commodity for reducing global carbon emissions.

the card should obviously have our logo and the theme should be sustainability/environment mixed with a trading platform.

Contact Information for Business Card

Logo, Name, Title, Phone, Email

Colors
0054AA
0677BA
7BADD7
CADEEF
E8F1F8
0094D4
00A9DD
6FCCEA
C7EBF8
E9F6FB
00AB8E
00BBA5
67D7C9
C6EFE9
E9F9F6
59FF00
82FF00
B8FF75
E3FFCB
F4FFEA

```html
<!DOCTYPE html>
<html lang="en">
<head>
<meta charset="UTF-8">
<title>Verodex Business Card</title>
<link href="https://fonts.googleapis.com/css2?family=Montserrat:wght@500;600&family=Raleway:wght@400;500&display=swap" rel="stylesheet">
<style>
  :root {
    --bg: #e9edf1;
    --card-white: #ffffff;
    --grad-start: #36e8ea;
    --grad-mid: #2aaee8;
    --grad-end: #1e6ff0;
    --navy: #172a44;
    --accent: #2f96e6;
    --line: #1a7fe0;
    --text-dark: #2a3342;
    --shadow: rgba(20, 40, 70, 0.18);
  }
  * { margin: 0; padding: 0; box-sizing: border-box; }
  html, body {
    width: 1200px;
    height: 977px;
    overflow: hidden;
    background: var(--bg);
  }
  .canvas {
    width: 1200px;
    height: 977px;
    display: flex;
    flex-direction: column;
    align-items: center;
    justify-content: center;
    gap: 48px;
  }
  .card {
    width: 640px;
    height: 366px;
    border-radius: 22px;
    position: relative;
    overflow: hidden;
    box-shadow: 0 14px 30px var(--shadow);
  }
  .card-front {
    background: linear-gradient(225deg, var(--grad-end) 0%, var(--grad-mid) 50%, var(--grad-start) 100%);
    display: flex;
    align-items: center;
    justify-content: center;
  }
  .brand {
    display: flex;
    align-items: center;
    gap: 22px;
    font-family: "Montserrat", sans-serif;
    font-weight: 600;
    letter-spacing: 0.02em;
    text-transform: uppercase;
  }
  .brand-mark {
    display: block;
    border-radius: 6px;
  }
  .card-front .brand { color: #ffffff; font-size: 70px; }
  .card-front .brand-mark { width: 70px; height: 70px; background: #ffffff; }

  .card-back { background: var(--card-white); }
  .card-back .brand {
    position: absolute;
    top: 44px;
    right: 48px;
    color: var(--navy);
    font-size: 38px;
    gap: 14px;
  }
  .card-back .brand-mark { width: 40px; height: 40px; background: var(--accent); border-radius: 4px; }

  .holder {
    position: absolute;
    left: 48px;
    top: 178px;
  }
  .holder-name {
    font-family: "Montserrat", sans-serif;
    font-weight: 600;
    font-size: 30px;
    color: var(--accent);
    text-transform: uppercase;
    letter-spacing: 0.01em;
  }
  .holder-title {
    font-family: "Raleway", sans-serif;
    font-weight: 500;
    font-size: 19px;
    color: var(--text-dark);
    margin-top: 2px;
  }
  .divider {
    position: absolute;
    left: 48px;
    right: 48px;
    top: 256px;
    height: 1.5px;
    background: var(--line);
  }
  .contacts {
    position: absolute;
    left: 48px;
    top: 272px;
    list-style: none;
    font-family: "Raleway", sans-serif;
    font-size: 16px;
    color: var(--text-dark);
    line-height: 1.5;
  }
  .contacts li { display: flex; align-items: center; gap: 10px; }
  .contacts svg { width: 14px; height: 14px; flex: none; }
</style>
</head>
<body>
<main class="canvas">
  <section class="card card-front" aria-label="Card front">
    <div class="brand"><span class="brand-mark"></span><span>Verodex</span></div>
  </section>

  <section class="card card-back" aria-label="Card back">
    <div class="brand"><span class="brand-mark"></span><span>Verodex</span></div>
    <div class="holder">
      <h1 class="holder-name">Daniel Reyes</h1>
      <p class="holder-title">Founder &amp; CEO</p>
    </div>
    <div class="divider"></div>
    <ul class="contacts">
      <li>
        <svg viewBox="0 0 16 16"><path d="M4 1.5l2.2 2.6-1.3 1.6a8 8 0 0 0 5.4 5.4l1.6-1.3 2.6 2.2-1.5 2.2C7.5 14 2 8.5 1.8 3z" fill="#2f96e6"/></svg>
        <span>(555) 210-4477</span>
      </li>
      <li>
        <svg viewBox="0 0 16 16"><rect x="1" y="3" width="14" height="10" rx="1" fill="#2f96e6"/><path d="M1.5 3.5L8 9l6.5-5.5" fill="none" stroke="#fff" stroke-width="1.3"/></svg>
        <span>office@verodex.com</span>
      </li>
      <li>
        <svg viewBox="0 0 16 16"><circle cx="8" cy="8" r="7" fill="#2f96e6"/><path d="M1 8h14M8 1c-3 3.5-3 10.5 0 14M8 1c3 3.5 3 10.5 0 14" fill="none" stroke="#fff" stroke-width="1"/></svg>
        <span>verodex.com</span>
      </li>
    </ul>
  </section>
</main>
</body>
</html>
```